velorahelp Web Design Project

It is a virtual assistance/concierge company that helps the busy professional by remotely providing administrative, technical and/or creative business support services, specializing in the medical device industry. Company name is velorahelp.
(website will be velorahelp.example)

Allowing things to be done without taking time away from more urgent issues or family/personal time. Partnering with a VA reduces stress, protects cash flow, eliminates administrative hassles, and enables business people to find the success they originally set out to achieve. Saves small businesses and/or individuals on overhead, salary, et. Work is done remotely to offer administrative, clerical, typing and specialist service assistance on a regular, ad-hoc or emergency cover basis.

Though we are capable of addressing the needs of medical professionals and industry representatives due to our experience and knowledge (sales, HCC guidelines, etc.) we do not want to be limited to that market only.

Target Market(s)

Target market would be M/F, 30-50, National, busy, Alpha, entrepreneurs and industry professionals who want/need to do more without sacrifice of life

Requirements
Nice to have
• We do have a logo designed via the PlanMarket website that can/should be included. Logo is uploaded.

```html
<!DOCTYPE html>
<html lang="en">
<head>
<meta charset="utf-8">
<title>velorahelp – Virtual Assistance</title>
<link rel="stylesheet" href="https://fonts.googleapis.com/css2?family=Open+Sans:wght@400;600;700&family=Tinos:ital,wght@0,400;1,400;1,700&display=swap">
<style>
  :root {
    --blue: #2b7fc4;
    --blue-dark: #1b5ea1;
    --navy: #1f3b78;
    --accent-red: #d6262f;
    --text: #333333;
    --muted: #666666;
    --line: #d5d5d5;
    --white: #ffffff;
    --page: #ffffff;
  }
  * { box-sizing: border-box; margin: 0; padding: 0; }
  html, body { width: 722px; height: 1200px; overflow: hidden; background: var(--page); }
  body { position: relative; font-family: "Open Sans", Verdana, sans-serif; color: var(--text); }
  .abs { position: absolute; }

  /* Header */
  .brand { left: 73px; top: 28px; display: flex; align-items: center; gap: 6px; }
  .brand-dot { width: 16px; height: 16px; border-radius: 50%; background: var(--accent-red); }
  .brand-name { font-size: 33px; font-weight: 600; color: var(--navy); letter-spacing: -0.5px; line-height: 44px; }
  .call-us { right: 70px; top: 27px; font-size: 12.5px; color: var(--blue); }
  .search { left: 517px; top: 50px; width: 136px; height: 26px; border: 1px solid #b5b5b5; border-radius: 5px;
            font-size: 11px; color: #666; padding: 5px 0 0 7px; box-shadow: inset 0 1px 2px rgba(0,0,0,.1); }
  .search svg { position: absolute; right: 7px; top: 6px; }

  /* Navigation */
  .nav { left: 73px; top: 93px; width: 579px; height: 46px; background: var(--blue); border-radius: 4px; }
  .nav-item { position: absolute; top: 0; height: 46px; line-height: 48px; font-size: 12.5px; color: var(--white); transform: translateX(-50%); }
  .nav-item.active { left: 5px; top: 5px; width: 125px; height: 36px; line-height: 38px; background: var(--white);
                     color: var(--blue); border-radius: 3px; text-align: center; transform: none; }

  /* Hero */
  .hero { left: 73px; top: 153px; width: 579px; height: 241px; box-shadow: 0 1px 4px rgba(0,0,0,.45);
          background: linear-gradient(90deg, #b48a62 0%, #8f7a6a 30%, #c4a27e 60%, #e7d2bf 80%, #f3ebe3 100%); }
  .dots { left: 346px; top: 406px; display: flex; gap: 3px; }
  .dots span { width: 8px; height: 8px; border-radius: 50%; background: #8c8c8c; }
  .dots span.on { background: var(--blue); }

  /* Feature columns */
  .feature { top: 452px; width: 181px; }
  .feature-title { font-family: "Tinos", "Times New Roman", serif; font-style: italic; font-weight: 700; font-size: 13px;
                   color: #222; text-align: center; height: 30px; }
  .feature-photo { width: 181px; height: 106px; border: 1px solid #bdbdbd; box-shadow: 0 1px 2px rgba(0,0,0,.2); }
  .feature-text { margin-top: 17px; font-size: 12px; line-height: 16px; color: var(--text); padding-left: 1px; }
  .btn-more { display: block; width: 51px; height: 25px; border: 1px solid #c2c2c2; border-radius: 5px; background: var(--white);
              font-size: 11px; line-height: 23px; text-align: center; color: var(--blue);
              box-shadow: -2px 0 0 #e2e2e2, 0 1px 2px rgba(0,0,0,.15); }
  .feature .btn-more { margin-top: 19px; }

  /* Section headings */
  .section-title { font-family: "Tinos", "Times New Roman", serif; font-size: 14px; color: #333; font-style: italic; }
  .section-title b { color: var(--blue); font-weight: 700; }

  .welcome { left: 75px; top: 737px; width: 380px; }
  .welcome p { margin-top: 9px; font-size: 12px; line-height: 20px; padding-left: 1px; }
  .welcome .btn-more { margin-top: 15px; }

  .services { left: 465px; top: 737px; width: 187px; }
  .service-list { list-style: none; margin-top: 13px; }
  .service-list li { display: flex; align-items: center; gap: 9px; font-size: 11.5px; height: 24.3px; }
  .services .btn-more { margin-top: 10px; }

  /* Clients */
  .clients { left: 73px; top: 959px; width: 580px; height: 155px; border: 1px solid #cfcfcf; border-radius: 4px;
             box-shadow: 0 1px 3px rgba(0,0,0,.25); }
  .clients .section-title { position: absolute; left: 11px; top: 7px; }
  .clients-rule { position: absolute; left: 11px; right: 14px; top: 30px; border-top: 1px solid var(--line); }
  .clients-arrows { position: absolute; right: 16px; top: 8px; display: flex; gap: 4px; }
  .client { position: absolute; top: 41px; width: 126px; }
  .client-photo { width: 126px; height: 74px; border: 1px solid #b9b9b9;
                  background: linear-gradient(135deg, #9ea39b 0%, #d7b69c 45%, #e9d5c5 70%, #c9ccc5 100%); }
  .client-name { margin-top: 10px; padding-left: 3px; font-family: "Tinos", "Times New Roman", serif; font-style: italic; font-size: 11px; color: #333; }

  /* Footer */
  .footer { left: 0; top: 1135px; width: 722px; height: 65px; background: linear-gradient(180deg, #3a88cc 0%, var(--blue-dark) 100%); color: #e6eef7; }
  .footer-brand { position: absolute; left: 77px; top: 6px; font-size: 12px; font-weight: 700; font-style: italic; text-decoration: underline; color: var(--white); }
  .footer-contact { position: absolute; left: 77px; top: 20px; font-size: 8.5px; line-height: 10.5px; }
  .find-us { position: absolute; left: 530px; top: 17px; display: flex; align-items: center; gap: 6px; font-size: 8.5px; }
  .social { width: 13px; height: 13px; border-radius: 3px; background: #1a4f8a; border: 1px solid #7fb0dd; }
  .copyright { position: absolute; left: 515px; top: 37px; font-size: 8.5px; }
</style>
</head>
<body>

<header>
  <div class="abs brand">
    <span class="brand-dot"></span>
    <span class="brand-name">velorahelp</span>
  </div>
  <div class="abs call-us">Call us @ 1800 - 55 - 017342</div>
  <div class="abs search">search...
    <svg width="13" height="13" viewBox="0 0 13 13"><circle cx="5" cy="5" r="3.8" fill="none" stroke="#888" stroke-width="1.6"/><line x1="8" y1="8" x2="12" y2="12" stroke="#888" stroke-width="2"/></svg>
  </div>
</header>

<nav class="abs nav">
  <span class="nav-item active">Home</span>
  <span class="nav-item" style="left:192px">About Us</span>
  <span class="nav-item" style="left:342px">Our Services</span>
  <span class="nav-item" style="left:489px">Contact Us</span>
</nav>

<div class="abs hero" role="img" aria-label="Smiling support agent with headset in front of a medical imaging room"></div>
<div class="abs dots"><span class="on"></span><span></span><span></span><span></span></div>

<section class="abs feature" style="left:74px">
  <h3 class="feature-title">Recieving calls</h3>
  <div class="feature-photo" role="img" aria-label="Agent with headset taking calls in an office" style="background:linear-gradient(90deg,#9aa3a6 0%,#b9a690 55%,#e4d8cc 100%)"></div>
  <p class="feature-text">Put here something about collection of client query or calls to researching over them in a brief.</p>
  <a class="btn-more">More</a>
</section>
<section class="abs feature" style="left:273px">
  <h3 class="feature-title">Reserching Issues</h3>
  <div class="feature-photo" role="img" aria-label="Man researching at a desk with two monitors" style="background:linear-gradient(90deg,#4c5a52 0%,#8e9aa6 40%,#c7b7a4 70%,#7d7f88 100%)"></div>
  <p class="feature-text">Put here something about researching of client query or calls to researching over them in a brief.</p>
  <a class="btn-more">More</a>
</section>
<section class="abs feature" style="left:471px">
  <h3 class="feature-title">Resolving Problems</h3>
  <div class="feature-photo" role="img" aria-label="Business handshake" style="background:radial-gradient(ellipse at 50% 50%,#cfe2f2 0%,#7fa8cc 55%,#26344a 100%)"></div>
  <p class="feature-text">Put here something about resolving of client query or calls to researching over them in a brief.</p>
  <a class="btn-more">More</a>
</section>

<section class="abs welcome">
  <h2 class="section-title"><b>Welcome</b> to our site</h2>
  <p>It is a virtual assistance/concierge company that helps the busy professional by remotely providing administrative, technical and/or creative business support services, specializing in the medical device industry. Company name is velorahelp. It is a virtual assistance/concierge company that helps the busy professional by remotely providing administrative, technical and/or creative business support services.</p>
  <a class="btn-more">More</a>
</section>

<section class="abs services">
  <h2 class="section-title"><b>Our</b> Services</h2>
  <ul class="service-list">
    <li><svg width="15" height="15" viewBox="0 0 15 15"><circle cx="7.5" cy="7.5" r="6.5" fill="#fff" stroke="#b8b8b8"/><path d="M6 4.5 L10 7.5 L6 10.5Z" fill="#4a8fc9"/></svg>Service goes here</li>
    <li><svg width="15" height="15" viewBox="0 0 15 15"><circle cx="7.5" cy="7.5" r="6.5" fill="#fff" stroke="#b8b8b8"/><path d="M6 4.5 L10 7.5 L6 10.5Z" fill="#4a8fc9"/></svg>Service goes here</li>
    <li><svg width="15" height="15" viewBox="0 0 15 15"><circle cx="7.5" cy="7.5" r="6.5" fill="#fff" stroke="#b8b8b8"/><path d="M6 4.5 L10 7.5 L6 10.5Z" fill="#4a8fc9"/></svg>Service goes here</li>
    <li><svg width="15" height="15" viewBox="0 0 15 15"><circle cx="7.5" cy="7.5" r="6.5" fill="#fff" stroke="#b8b8b8"/><path d="M6 4.5 L10 7.5 L6 10.5Z" fill="#4a8fc9"/></svg>Service goes here</li>
    <li><svg width="15" height="15" viewBox="0 0 15 15"><circle cx="7.5" cy="7.5" r="6.5" fill="#fff" stroke="#b8b8b8"/><path d="M6 4.5 L10 7.5 L6 10.5Z" fill="#4a8fc9"/></svg>Service goes here</li>
    <li><svg width="15" height="15" viewBox="0 0 15 15"><circle cx="7.5" cy="7.5" r="6.5" fill="#fff" stroke="#b8b8b8"/><path d="M6 4.5 L10 7.5 L6 10.5Z" fill="#4a8fc9"/></svg>Service goes here</li>
  </ul>
  <a class="btn-more">More</a>
</section>

<section class="abs clients">
  <h2 class="section-title"><b>Our</b> Clients</h2>
  <div class="clients-arrows">
    <svg width="14" height="14" viewBox="0 0 14 14"><circle cx="7" cy="7" r="6" fill="#fff" stroke="#b8b8b8"/><path d="M8.5 4 L4.5 7 L8.5 10Z" fill="#4a8fc9"/></svg>
    <svg width="14" height="14" viewBox="0 0 14 14"><circle cx="7" cy="7" r="6" fill="#fff" stroke="#b8b8b8"/><path d="M5.5 4 L9.5 7 L5.5 10Z" fill="#4a8fc9"/></svg>
  </div>
  <div class="clients-rule"></div>
  <div class="client" style="left:10px"><div class="client-photo" role="img" aria-label="Client portrait"></div><p class="client-name">Meadowbrook Clinic</p></div>
  <div class="client" style="left:154px"><div class="client-photo" role="img" aria-label="Client portrait"></div><p class="client-name">Meadowbrook Clinic</p></div>
  <div class="client" style="left:298px"><div class="client-photo" role="img" aria-label="Client portrait"></div><p class="client-name">Meadowbrook Clinic</p></div>
  <div class="client" style="left:439px"><div class="client-photo" role="img" aria-label="Client portrait"></div><p class="client-name">Meadowbrook Clinic</p></div>
</section>

<footer class="abs footer">
  <span class="footer-brand">velorahelp</span>
  <div class="footer-contact">Emergency Call : 1800-00-0418<br>Fax : 6510047723<br>E-mail : help4@velorahelp.example</div>
  <div class="find-us">Find Us : <span class="social"></span><span class="social"></span><span class="social"></span></div>
  <div class="copyright">Copyright 2012 | Privacy Policy</div>
</footer>

</body>
</html>
```